Website Design for Solar Panel Company

We are working with a company called VoltaNix.

Some sites to use for content/competitors and inspiration:
https://www.brivaloo.com
https://prod.aws-prod.kelmatrix.com
https://tovarqueworks.net
https://www.quorvex.com/solarpanels

Thank you for taking the time to consider designing a website for us. We are web developers based in Stockton, CA, USA. Most of our projects go through the same process. Understanding this process may help you win a project with us. We custom-code all of our websites in-house. We don’t have any requirements as to what tools you use for your design, but we prefer Figma files. For any design that we label as four-stars, we send it to the client for review. The client picks the final design they want us to use. Once we complete this process, we will continue to show additional clients all the four-star sites and purchase them later. Your designs will have multiple chances to sell. For better chances of success, we ask that you follow these guidelines.

IMAGES:
If you use any images or icons in the design, we ask that you have a link to the asset so we can purchase the image/icon. Most of the designs we submit do not have the customer’s images on them unless they have some great images. Be creative; show us the feeling you are trying to portray with your image choices. Use any royalty-free site you choose. We subscribe to Pendrel and mainly use their images, but we can purchase images outside of Pendrel. PLEASE NOTE: we will not submit designs to clients with watermarks on the images.

FONTS:
We ask that you identify the fonts used in the design. This can be done in a message if you want. We typically use Google Fonts and Pendrel Fonts.

CONTENT:
We're always open to different content and ideas. We often submit designs with stock images so the client can see our vision. We typically take pictures after the website launch to use their images with our vision. Lorem Ipsum is fine for paragraphs, but we ask that you write the headers in correct English. We want to be able to show the vision and identify the sections of the website.

INSPIRATION:
We typically add a couple of links in the brief of websites we like to help you get started in your design.

REVISIONS:
We do not often ask for revisions of the designs unless we see something in the design that may not appeal to the client. If there are slight changes that we want to make, we do that in the development process.

FEEDBACK:
We rarely give feedback on designs during the design process. We are working on many website projects and do not have the time to provide feedback. We usually respond if your request is well thought out and asks specific questions, but a note asking “feedback, please” usually goes unanswered.

```html
<!DOCTYPE html>
<html lang="en">
<head>
<meta charset="UTF-8">
<title>VoltaNix — Solar Panels For Your Home</title>
<link href="https://fonts.googleapis.com/css2?family=Black+Ops+One&family=Roboto:wght@400;500;700&display=swap" rel="stylesheet">
<style>
:root{
  --green:#3dbb1c;
  --green-bright:#5bdc0c;
  --green-dark:#1f6e0c;
  --black:#000;
  --panel:#0d0d0d;
  --card:#141414;
  --field:#1c1c1c;
  --white:#fff;
  --muted:#d9d9d9;
}
*{box-sizing:border-box;margin:0;padding:0}
html,body{width:1200px;height:4251px;overflow:hidden;background:var(--black);color:var(--white);font-family:"Roboto",Arial,sans-serif}
.section{position:relative;width:1200px;overflow:hidden}
.heading{font-family:"Black Ops One",Impact,sans-serif;font-weight:400;letter-spacing:2px;text-align:center;font-size:38px;line-height:48px;position:absolute;left:0;right:0}
.btn{display:inline-flex;align-items:center;gap:12px;background:linear-gradient(90deg,var(--green-dark),var(--green-bright));color:var(--white);font-size:13px;font-weight:700;text-transform:uppercase;border-radius:24px;padding:0 10px 0 22px;height:40px;position:absolute}
.power{width:24px;height:24px}
.brand{font-family:"Roboto",Arial,sans-serif;font-weight:700;font-size:44px;letter-spacing:1px;color:var(--white);position:absolute}

/* header */
.site-header{height:127px;background:var(--black)}
.header-bar{position:absolute;left:470px;top:0;width:730px;height:55px;background:#111}
.util{position:absolute;top:14px;display:flex;align-items:center;gap:10px;font-size:12px;font-weight:700;text-transform:uppercase}
.util .dot{width:28px;height:28px;border-radius:50%;background:var(--green);display:flex;align-items:center;justify-content:center}
.nav{position:absolute;top:80px;left:370px;display:flex;gap:44px;font-size:13px;font-weight:700}
.nav a{color:var(--white);text-decoration:none}

/* hero */
.hero{height:617px}
.hero-photo{position:absolute;inset:0;background:linear-gradient(90deg,#1a2417 0%,#3b4a3c 35%,#6a7a86 60%,#5a6b7c 100%)}
.hero h1{position:absolute;left:112px;top:186px;font-family:"Black Ops One",Impact,sans-serif;font-weight:400;font-size:58px;line-height:74px;letter-spacing:3px}
.hero p{position:absolute;left:112px;top:354px;font-size:27px;font-weight:500}

/* features */
.features{height:228px;display:flex;background:linear-gradient(180deg,#0a1f05,#123d08)}
.feature{flex:1;display:flex;flex-direction:column;align-items:center;justify-content:center;gap:22px;text-align:center;font-size:16px;font-weight:700;line-height:26px;border-right:2px solid var(--green)}
.feature:last-child{border-right:0}

/* services */
.services{height:594px;background:#060606}
.svc{position:absolute;top:186px;width:286px;height:327px}
.svc .box{position:absolute;left:0;right:0;bottom:0;height:195px;background:var(--card);border-radius:6px}
.svc .pic{position:absolute;left:19px;top:0;width:248px;height:248px;border-radius:50%;border:7px solid var(--green)}
.svc .tab{position:absolute;left:127px;top:222px;width:32px;height:56px;border-radius:16px;background:var(--green);border:5px solid #0a0a0a}
.svc .label{position:absolute;bottom:30px;left:0;right:0;text-align:center;font-size:14px;font-weight:700}
.arrow{position:absolute;width:38px;height:38px;border-radius:50%;background:#1a1a1a;display:flex;align-items:center;justify-content:center;font-size:14px;font-weight:700}

/* why */
.why{height:810px;background:var(--black)}
.node{position:absolute;width:118px;height:118px;border-radius:50%;background:linear-gradient(135deg,#52d414,#166a06);display:flex;align-items:center;justify-content:center}
.node-label{position:absolute;font-size:15px;font-weight:700}

/* testimonials */
.testimonials{height:480px;background:linear-gradient(90deg,#1d7a09,#3fbe0c 50%,#58d80a)}
.testimonials .heading{color:#0b0b0b}
.quote{position:absolute;top:158px;width:299px;height:174px;background:#0c0c0c;border-radius:8px 8px 36px 8px;padding:42px 22px 0}
.quote .avatar{position:absolute;left:22px;top:-8px;width:48px;height:48px;border-radius:50%;background:linear-gradient(#c7d5e6,#2d4c7a)}
.quote .name{position:absolute;left:84px;top:20px;font-size:12px;font-weight:700}
.quote p{font-size:13px;line-height:25px;color:var(--muted);margin-top:8px}
.quote a{font-size:12px;color:var(--muted);display:block;margin-top:8px;text-decoration:underline}

/* questions */
.questions{height:370px;background:var(--black)}
.questions p{position:absolute;left:230px;width:740px;top:170px;text-align:center;font-size:13px;line-height:26px;color:var(--muted)}

/* contact */
.contact{height:640px;background:var(--panel)}
.offer{position:absolute;left:109px;top:194px;width:404px;height:274px;background:linear-gradient(135deg,#3fbe0c,#56d80a);text-align:center;padding-top:48px}
.offer h3{font-size:28px;line-height:44px;font-weight:700;color:#0d2a02}
.form-panel{position:absolute;left:426px;top:219px;width:717px;height:322px;background:#020202}
.field{position:absolute;height:46px;border-radius:23px;background:var(--field);font-size:12px;font-weight:500;padding:16px 34px;text-transform:uppercase}

/* footer */
.footer{height:385px;background:var(--black)}
.fcol{position:absolute;top:100px;font-size:13px;line-height:25px}
.fcol h4{font-size:13px;font-weight:700;margin-bottom:10px}
.copyright{position:absolute;top:324px;left:0;right:0;text-align:center;font-size:11px}
</style>
</head>
<body>

<header class="section site-header">
  <div class="brand" style="left:110px;top:32px;font-size:40px">VoltaNix</div>
  <div class="header-bar"></div>
  <div class="util" style="left:622px"><span class="dot">$</span>Pay My Bill</div>
  <div class="util" style="left:796px"><span class="dot"><svg width="12" height="12" viewBox="0 0 12 12"><circle cx="6" cy="4" r="3" fill="#fff"/><path d="M1 12a5 5 0 0110 0z" fill="#fff"/></svg></span>Log In</div>
  <div class="util" style="left:925px"><span class="dot"><svg width="13" height="13" viewBox="0 0 24 24"><path d="M6.6 10.8a15 15 0 006.6 6.6l2.2-2.2a1 1 0 011-.25 11.4 11.4 0 003.6.6 1 1 0 011 1V20a1 1 0 01-1 1A17 17 0 013 4a1 1 0 011-1h3.5a1 1 0 011 1c0 1.25.2 2.45.6 3.6a1 1 0 01-.25 1z" fill="#fff"/></svg></span>+1 (555) 014 2290</div>
  <nav class="nav"><a>Home</a><a>About</a><a>Buy/Sell Solar Panel</a><a>FAQ</a><a>Gallery</a><a>Reviews</a></nav>
  <span class="btn" style="left:919px;top:70px;height:42px">Contact Us <svg class="power" viewBox="0 0 24 24"><path d="M7.5 6.5a8 8 0 109 0" fill="none" stroke="#fff" stroke-width="3" stroke-linecap="round"/><path d="M12 3v9" stroke="#fff" stroke-width="3" stroke-linecap="round"/></svg></span>
</header>

<section class="section hero">
  <div class="hero-photo" role="img" aria-label="Smiling couple in front of a house with rooftop solar panels"></div>
  <h1>SOLAR PANELS<br>FOR YOUR HOME</h1>
  <p>Lowest Cost Solar Panels in America</p>
  <span class="btn" style="left:114px;top:422px">Get Started <svg class="power" viewBox="0 0 24 24"><path d="M7.5 6.5a8 8 0 109 0" fill="none" stroke="#fff" stroke-width="3" stroke-linecap="round"/><path d="M12 3v9" stroke="#fff" stroke-width="3" stroke-linecap="round"/></svg></span>
</section>

<section class="section features">
  <div class="feature"><svg width="56" height="60" viewBox="0 0 56 60" fill="none" stroke="#fff" stroke-width="3"><path d="M20 12h12l-4-8h-4z"/><path d="M18 14c-12 10-14 40 8 40s20-30 8-40z"/><text x="26" y="42" fill="#fff" stroke="none" font-size="18" font-family="Roboto" text-anchor="middle">$</text><path d="M46 26v24m-6-6l6 6 6-6"/></svg><span>Guaranteed Lowest<br>Price in America</span></div>
  <div class="feature"><svg width="58" height="60" viewBox="0 0 58 60" fill="none" stroke="#fff" stroke-width="3"><path d="M29 4l22 13v26L29 56 7 43V17z"/><path d="M29 18l10 6v12l-10 6-10-6V24z"/><circle cx="29" cy="4" r="3" fill="#fff"/><circle cx="51" cy="43" r="3" fill="#fff"/><circle cx="7" cy="43" r="3" fill="#fff"/></svg><span>Integrated<br>Product Ecosystem</span></div>
  <div class="feature"><svg width="58" height="60" viewBox="0 0 58 60" fill="none" stroke="#fff" stroke-width="3"><path d="M50 22a24 24 0 11-10-12"/><text x="3" y="24" fill="#fff" stroke="none" font-size="20" font-weight="700" font-family="Roboto">24</text><path d="M32 34h12l-8 14" stroke-width="3"/></svg><span>System Performance<br>Monitoring</span></div>
</section>

<section class="section services">
  <h2 class="heading" style="top:80px">OUR SERVICES</h2>
  <span class="arrow" style="left:32px;top:257px">«</span>
  <span class="arrow" style="left:1129px;top:257px">»</span>
  <div class="svc" style="left:114px"><div class="box"></div><div class="pic" role="img" aria-label="Technician levelling a solar panel" style="background:linear-gradient(160deg,#bcd4ea,#3d6ea8 60%,#c56a2a)"></div><div class="tab"></div><div class="label">Lorem ipsum dolor sit</div></div>
  <div class="svc" style="left:457px"><div class="box"></div><div class="pic" role="img" aria-label="Installer on a roof fitting solar panels" style="background:linear-gradient(180deg,#7fb7e8,#4a7a3a 55%,#2b4d8c)"></div><div class="tab"></div><div class="label">Lorem ipsum dolor sit</div></div>
  <div class="svc" style="left:800px"><div class="box"></div><div class="pic" role="img" aria-label="Gloved hands installing a solar panel" style="background:linear-gradient(160deg,#c98a55,#7a4a28 50%,#2a3a5c)"></div><div class="tab"></div><div class="label">Lorem ipsum dolor sit</div></div>
</section>

<section class="section why">
  <h2 class="heading" style="top:86px">WHY CHOOSE US</h2>
  <svg width="1200" height="810" style="position:absolute;left:0;top:0" fill="none" stroke="#3dbb1c" stroke-width="2">
    <path d="M338 300H503M695 300H858"/>
    <path d="M402 300a196 196 0 00392 0"/>
    <path d="M467 447L403 477M731 447L797 477M598 496V568"/>
    <g fill="#3dbb1c" stroke="none"><circle cx="402" cy="300" r="11"/><circle cx="794" cy="300" r="11"/><circle cx="467" cy="447" r="11"/><circle cx="731" cy="447" r="11"/><circle cx="598" cy="496" r="11"/></g>
    <circle cx="599" cy="299" r="96" stroke="#9ef27a" stroke-width="4" fill="#080808"/>
    <circle cx="599" cy="299" r="80" stroke="#3dbb1c" stroke-width="3"/>
    <circle cx="599" cy="299" r="54" fill="#2ea612" stroke="none"/>
    <path d="M575 275a34 34 0 1048 0" stroke="#0b0b0b" stroke-width="12" stroke-linecap="round"/>
    <path d="M599 255v44" stroke="#0b0b0b" stroke-width="12" stroke-linecap="round"/>
  </svg>
  <div class="node" style="left:220px;top:241px"><svg width="54" height="64" viewBox="0 0 54 64" fill="none" stroke="#fff" stroke-width="2.5"><rect x="4" y="4" width="46" height="56"/><rect x="10" y="10" width="34" height="44"/><circle cx="27" cy="26" r="8"/><path d="M16 42h22M16 48h22"/></svg></div>
  <div class="node-label" style="left:62px;top:290px">Lorem ipsum dolor</div>
  <div class="node" style="left:858px;top:241px"><svg width="64" height="64" viewBox="0 0 64 64" fill="none" stroke="#fff" stroke-width="2.5"><circle cx="32" cy="32" r="27" stroke-dasharray="8 4"/><circle cx="32" cy="32" r="19"/><path d="M23 32l6 6 12-12"/></svg></div>
  <div class="node-label" style="left:997px;top:290px">Lorem ipsum dolor</div>
  <div class="node" style="left:292px;top:438px"><svg width="64" height="60" viewBox="0 0 64 60" fill="none" stroke="#fff" stroke-width="2.5"><circle cx="38" cy="18" r="14"/><text x="38" y="25" fill="#fff" stroke="none" font-size="18" text-anchor="middle" font-family="Roboto">$</text><path d="M4 44h12l10 4h14a4 4 0 010 8H24M40 52l16-8a4 4 0 014 6L40 60H4"/></svg></div>
  <div class="node-label" style="left:140px;top:521px">Lorem ipsum dolor</div>
  <div class="node" style="left:786px;top:438px"><svg width="50" height="60" viewBox="0 0 50 60" fill="none" stroke="#fff" stroke-width="2.5"><path d="M25 4l20 8v18c0 14-10 22-20 26C15 52 5 44 5 30V12z"/><path d="M16 30l6 6 12-12"/></svg></div>
  <div class="node-label" style="left:929px;top:521px">Lorem ipsum dolor</div>
  <div class="node" style="left:549px;top:568px"><svg width="64" height="60" viewBox="0 0 64 60" fill="none" stroke="#fff" stroke-width="2.5"><path d="M6 30h10v26H6zM16 32l10-14c2-6 8-6 8 0l-2 10h14a4 4 0 010 8 4 4 0 010 8 4 4 0 010 8H16"/><path d="M50 4l3 7 7 1-5 5 1 7-6-3-6 3 1-7-5-5 7-1z"/></svg></div>
  <div class="node-label" style="left:543px;top:710px">Lorem ipsum dolor</div>
</section>

<section class="section testimonials">
  <h2 class="heading" style="top:74px">OUR TESTIMONIALS</h2>
  <div class="quote" style="left:109px"><span class="avatar" role="img" aria-label="Customer portrait"></span><span class="name">MARLO VENKIRK</span><p>Lorem ipsum dolor sit amet, consectetur adipiscing elit, sed do eiusmod tempor incididunt ut labore</p><a>Read More</a></div>
  <div class="quote" style="left:448px"><span class="avatar" role="img" aria-label="Customer portrait"></span><span class="name">MARLO VENKIRK</span><p>Lorem ipsum dolor sit amet, consectetur adipiscing elit, sed do eiusmod tempor incididunt ut labore</p><a>Read More</a></div>
  <div class="quote" style="left:787px"><span class="avatar" role="img" aria-label="Customer portrait"></span><span class="name">MARLO VENKIRK</span><p>Lorem ipsum dolor sit amet, consectetur adipiscing elit, sed do eiusmod tempor incididunt ut labore</p><a>Read More</a></div>
  <span class="arrow" style="left:534px;top:357px;background:#0a0a0a">«</span>
  <svg style="position:absolute;left:584px;top:372px" width="32" height="8"><circle cx="4" cy="4" r="3.5" fill="#0a0a0a"/><circle cx="16" cy="4" r="3.5" fill="#0a0a0a"/><circle cx="28" cy="4" r="3.5" fill="#0a0a0a"/></svg>
  <span class="arrow" style="left:627px;top:357px;background:#0a0a0a">»</span>
</section>

<section class="section questions">
  <h2 class="heading" style="top:80px">QUESTIONS ABOUT SOLAR?</h2>
  <p>Have a no obligation conversation with a solar professional privately and get answers to any questions or concerns you may have. It's that simple.</p>
  <span class="btn" style="left:498px;top:244px">Lets Talk Solar <svg class="power" viewBox="0 0 24 24"><path d="M7.5 6.5a8 8 0 109 0" fill="none" stroke="#fff" stroke-width="3" stroke-linecap="round"/><path d="M12 3v9" stroke="#fff" stroke-width="3" stroke-linecap="round"/></svg></span>
</section>

<section class="section contact">
  <h2 class="heading" style="top:86px;left:26px">GET IN TOUCH</h2>
  <div class="form-panel"></div>
  <div class="offer">
    <h3>GET RECORD-BREAKING<br>HOME SOLAR &amp; SAVE<br>MORE</h3>
    <span class="btn" style="left:119px;top:190px;background:linear-gradient(90deg,#1a5e08,#4cc20f)">Contact Us <svg class="power" viewBox="0 0 24 24"><path d="M7.5 6.5a8 8 0 109 0" fill="none" stroke="#fff" stroke-width="3" stroke-linecap="round"/><path d="M12 3v9" stroke="#fff" stroke-width="3" stroke-linecap="round"/></svg></span>
  </div>
  <div class="field" style="left:548px;top:264px;width:277px">Name</div>
  <div class="field" style="left:840px;top:264px;width:277px">Email</div>
  <div class="field" style="left:548px;top:330px;width:277px">Phone</div>
  <div class="field" style="left:840px;top:330px;width:277px">Address</div>
  <div class="field" style="left:548px;top:392px;width:569px;height:94px;border-radius:24px">Message</div>
  <span class="btn" style="left:736px;top:514px;height:43px;padding-left:38px;width:167px">Submit <svg class="power" viewBox="0 0 24 24"><path d="M7.5 6.5a8 8 0 109 0" fill="none" stroke="#fff" stroke-width="3" stroke-linecap="round"/><path d="M12 3v9" stroke="#fff" stroke-width="3" stroke-linecap="round"/></svg></span>
</section>

<footer class="section footer">
  <div class="brand" style="left:110px;top:168px">VoltaNix</div>
  <div class="fcol" style="left:399px"><h4>QUICK LINKS</h4>Home<br>About<br>Buy/Sell Solar Panel<br>FAQ<br>Gallery<br>Reviews</div>
  <div class="fcol" style="left:596px"><h4>OTHER LINKS</h4>Find a Kelsol Solar Dealer by Zip<br>Find a Local Kelsol Master Dealer<br>Become a Kelsol Dealer<br>Become a Kelsol Installer<br>Dealer Portal Login<br>Kelsol Monitoring for Dealers</div>
  <div class="fcol" style="left:929px"><h4>CONTACT</h4>Lorem ipsum dolor sit amet,<br>consectetur adipiscing<br><b style="line-height:32px">+1 (555) 014 2290</b><br><b style="line-height:32px">info@voltanix.com</b><br>
    <svg width="66" height="14" style="margin-top:8px"><circle cx="6" cy="7" r="5" fill="#fff"/><circle cx="32" cy="7" r="5" fill="#fff"/><circle cx="58" cy="7" r="5" fill="#fff"/></svg></div>
  <div class="copyright">Copyright@2024 All Rights By VoltaNix.</div>
</footer>

</body>
</html>
```